Product Description page for Hullwrap.com, References here just need a clean up redesign

Hi, were working on updating the product description page of our site hullwrap.com

Attached is a reference of what we drew on paint. We want to keep it pretty much the same as far as whats on there, the components with a few small adjustments and a clean actually designed look.

1. We want to remove the tabs (product description, warranty, reviews) and put it all in that main content area stretching down into sections. IE: Product Description section, followed by reviews, followed by warranty, below each other.
2. The side bar needs to be redesigned as far as the look and feel but the content and whats in there should stay the same.
3. The main banner area will be replaced shortly you do not have to worry about that.
4. Include a section or box for people to put in their email for a free Ebook.

Target Market(s)

people looking to easily view our boat cover products and buy without having to click too often or leave the page.

Industry/Entity Type

Online Shopping

Number of Pages Required

1 page

Requirements
Must have
• - Must update the sidebar
• - Must update the content area to remove the tabs and put the content from each tab sectioned off below each other (dummy text is fine for now for the tabs you cant view)
Nice to have
• - Cool place thats clean and functional to insert a section for people to put in their email to receive a free ebook
Should not have
• - too much change, we already know what we want and have a solid reference to work from.

```html
<!DOCTYPE html>
<html lang="en">
<head>
<meta charset="utf-8">
<title>Hullwrap.com – Product Page</title>
<link rel="stylesheet" href="https://fonts.googleapis.com/css2?family=Lato:wght@400;700&display=swap">
<style>
:root{
  --page-bg:#f5f5f5;
  --panel:#ffffff;
  --rule:#8a8a8a;
  --text:#3c3c3c;
  --heading-blue:#2a8fc0;
  --news-blue:#2b6a8e;
  --link-blue:#1a22b0;
  --star-gold:#f3d23a;
  --star-gray:#b9b9b9;
  --green-a:#b6e26a;
  --green-b:#7cc428;
  --orange:#ff6a00;
  --footer-line:#28b6e8;
  --copy:#9aa6d6;
}
*{box-sizing:border-box;margin:0;padding:0}
html,body{width:1200px;height:1185px;overflow:hidden}
body{background:var(--page-bg);font-family:'Lato',sans-serif;color:var(--text);position:relative}
.abs{position:absolute}
.content-panel{left:216px;top:-2px;width:768px;height:771px;background:var(--panel);border:1px solid var(--rule)}
.short-rule{height:1px;background:#2a2f6a;left:268px;width:427px}
.review-text{left:233px;width:500px;font-size:14px;line-height:17.5px}
.quote{color:var(--link-blue)}
.reviewer{font-size:14px;color:var(--link-blue)}
.stars{width:72px;height:18px}
.full-rule{left:216px;width:768px;height:1px;background:var(--rule);top:164px}
.section-title{left:232px;top:184px;font-size:19.5px;font-weight:700;color:var(--heading-blue)}
.sub-title{left:232px;font-size:14px;font-weight:700;color:#333}
.para{left:231px;width:585px;font-size:14px;line-height:17.3px}
.newsletter{left:0;top:796px;width:1200px;height:110px;background:#fff}
.news-title{left:264px;top:808px;font-size:23.5px;font-weight:700;color:var(--news-blue)}
.news-sub{left:264px;top:838px;font-size:13.6px;line-height:17px;color:#333}
.email-pill{left:638px;top:815px;width:289px;height:60px;border:1px solid #9a9a9a;border-radius:30px;background:#fff}
.email-pill span{position:absolute;left:20px;top:20px;font-size:14px;color:#9a9a9a}
.signup-btn{position:absolute;left:150px;top:10px;width:130px;height:38px;border-radius:19px;background:linear-gradient(var(--green-a),var(--green-b));color:#fff;font-weight:700;font-size:20px;text-align:center;line-height:38px}
.harbor-scene{left:0;top:896px;width:1200px;height:289px;
  background:linear-gradient(180deg,#ffffff 0%,#dfe6ee 6%,#a9b9cc 14%,#8ea4bc 22%,#5d7560 28%,#3f5e3a 32%,#8b9fc0 34%,#2f5fae 42%,#1a46a2 60%,#0e2f8e 100%)}
.footer-bar{left:218px;top:1048px;width:767px;height:49px;border:1px solid var(--footer-line);border-radius:12px}
.footer-promo{left:233px;top:1062px;font-size:14px;color:#fff}
.footer-input{left:464px;top:1058px;width:136px;height:29px;background:#fff;border-radius:4px}
.footer-btn{left:598px;top:1057px;width:88px;height:30px;background:var(--orange);border-radius:3px;color:#fff;font-weight:700;font-size:15px;text-align:center;line-height:30px}
.footer-link{top:1062px;font-size:14px;color:#fff;text-decoration:underline}
.copyright{left:0;width:1200px;top:1133px;text-align:center;font-size:11px;line-height:13.5px;color:var(--copy)}
.copyright a{color:#fff;text-decoration:underline}
</style>
</head>
<body>
<svg width="0" height="0" style="position:absolute">
  <defs>
    <polygon id="star" points="9,1 11.3,6.5 17,7 12.6,10.8 14,16.5 9,13.4 4,16.5 5.4,10.8 1,7 6.7,6.5"/>
  </defs>
</svg>

<div class="abs content-panel"></div>
<div class="abs short-rule" style="top:0"></div>

<p class="abs review-text" style="top:12px"><span class="quote">“</span> Great cover and very nice fit. Would buy again if needed. Highly recommend this cover. Ties down tight and snug. Very high quality cover!.<span class="quote">”</span></p>
<span class="abs reviewer" style="left:602px;top:50px">Warren</span>
<svg class="abs stars" style="left:651px;top:49px" viewBox="0 0 72 18">
  <use href="#star" x="0" fill="var(--star-gold)" stroke="#c9a21a" stroke-width=".6"/>
  <use href="#star" x="17.5" fill="var(--star-gold)" stroke="#c9a21a" stroke-width=".6"/>
  <use href="#star" x="35" fill="var(--star-gold)" stroke="#c9a21a" stroke-width=".6"/>
  <use href="#star" x="52.5" fill="var(--star-gold)" stroke="#c9a21a" stroke-width=".6"/>
</svg>

<div class="abs short-rule" style="top:81px"></div>

<p class="abs review-text" style="top:92px"><span class="quote">“</span> I bought 2 of these for 2 boats I own. They have been fabulous so far. We will see how they survive the winter.<span class="quote">”</span></p>
<span class="abs reviewer" style="left:602px;top:122px">Mateo</span>
<svg class="abs stars" style="left:651px;top:120px" viewBox="0 0 72 18">
  <use href="#star" x="0" fill="var(--star-gold)" stroke="#c9a21a" stroke-width=".6"/>
  <use href="#star" x="17.5" fill="var(--star-gold)" stroke="#c9a21a" stroke-width=".6"/>
  <use href="#star" x="35" fill="var(--star-gold)" stroke="#c9a21a" stroke-width=".6"/>
  <use href="#star" x="52.5" fill="var(--star-gray)" stroke="#999" stroke-width=".6"/>
</svg>

<div class="abs full-rule"></div>

<h2 class="abs section-title">Warranty :</h2>

<h3 class="abs sub-title" style="top:219px">Returns &amp; Refunds</h3>
<p class="abs para" style="top:243px;left:230px">If you are not 100% satisfied with your purchase, you can return or exchange your order. (Returns must be unworn, in the state you received them, and in the original packaging). Hullwrap Covers will process all returns and refunds within 30 days of original order date. After 30 days all orders are final. For the full details on our returns or exchange policy please read below.Hullwrap Covers guarantees the covers you purchase will arrive in new condition, be free of defects and will properly fit the vehicle for which you ordered. If your item fails to meet the criteria above Hullwrap Covers will exchange or return the item.</p>

<h3 class="abs sub-title" style="top:400px">Returning Titan Crest Covers</h3>
<p class="abs para" style="top:424px;left:232px">Titan Crest covers are 5 Star Fit Covers. The fit and quality are 100% guaranteed or your money back. You have 30 days to try the cover. if you are not 100% satisfied feel free to return or exchange it hassle free. No restocking fee’s, we even pay for the shipping.</p>

<h3 class="abs sub-title" style="top:494px">Returning MarinaFit Covers</h3>
<p class="abs para" style="top:521px;left:232px">MarinaFit covers are 4 Star Fit Covers. MarinaFit covers are semi custom covers based on boat style, length and width. The cover is fully exchangeable.. A small 15% restocking fee is applied when returning or exchanging this cover. You have 30 days to return or exchange the cover. If you are not 100% satisfied, give us a call and will help return or exchange it. We even pay for the shipping.</p>

<h3 class="abs sub-title" style="top:626px">Returning Sunvale Covers</h3>
<p class="abs para" style="top:652px;left:232px">MarinaFit covers are 3 Star Fit Covers. Sunvale covers are universal covers based on length and width. A small 15% restocking fee is applied when returning or exchanging this cover. You have 30 days to return or exchange the cover. If you are not 100% satisfied, give us a call and will help return or exchange it. We even pay for the shipping.</p>

<section class="abs newsletter"></section>
<h2 class="abs news-title">Subscribe To Our News Letter</h2>
<p class="abs news-sub">and recieve great tips on how to<br>grow your business online</p>
<div class="abs email-pill"><span>Enter Your Email</span><div class="signup-btn">Sign Up</div></div>

<div class="abs harbor-scene" role="img" aria-label="Harbor scene with misty mountains, a wooded shoreline, moored sailboats and deep blue water"></div>

<div class="abs footer-bar"></div>
<p class="abs footer-promo">sign up to win <b>A FREE</b> boat cover !</p>
<div class="abs footer-input"></div>
<div class="abs footer-btn">Subscribe</div>
<a class="abs footer-link" style="left:741px">exchanges &amp; returns</a>
<a class="abs footer-link" style="left:887px">contact us</a>

<p class="abs copyright">copyright ©&nbsp; 2016 hullwrap.com all rights reserved<br>218 east harbor lane,port ellis NY 10412<br><a>privacy policy</a></p>
</body>
</html>
```